Industry / Entity Type

Financial consultancy / advisers

Current site is: http://www.brightmoor-counsel.com

Looking for a complete overhaul of this site, we are after a clean modern look. Will require the ability to easily add, update and remove content, hence the WordPress design.
Example:
Add case studies
Industry documentation (downloadable brochures / flyers and such)

What we like from our current site is the colour the fonts and the logo (the city of London) we would like to have other city outlines (NYC and Tokyo, Hong Kong, Singapore).

The site will be used by our potential clients to get in contact and re-view the case studies, if possible would like to have a client login area where they can download our documents like NDA’s etc and T&C’s.

Task Outline

Create a Web Design (Coded - Design and coding required)
Designer must provide full implementation/coding depending on the platform chosen by the client (i.e. WordPress theme, HTML/CSS, bootstrap etc.)

Task Description

I need a full website built that must work on desktop and mobile. I can provide the London city skyline and the font file, which we have used. Some stock industrial photos will be required.

Requirements:

*Splash page
*What We Do
*How We do it
*Who Are We? To have the same information and links as the current site
*Why use us?
*Clients: To have the same information and links as the current site
*Partners: To have the same information and links as the current site
*Contact:

Target Market(s)

Financial institutions trading Equities, Futures, Options, Forex and Fixed Income.
Regulators, Exchanges, ECN’s
Buy side firms and Sell side firms

Industry/Entity Type

Financial

Coding

Coded - Design and coding required

Number of Pages Required

5+ page

Font styles to use
Sans Serif

Colors
f04a50

Requirements
Must have
• Splash page
• What We Do
• How We do it
• Who Are We? To have the same information and links as the current site
• Why use us?
• Clients: To have the same information and links as the current site
• Partners: To have the same information and links as the current site
• Contact:

```html
<!DOCTYPE html>
<html lang="en">
<head>
<meta charset="utf-8">
<title>Brightmoor Counsel</title>
<link href="https://fonts.googleapis.com/css2?family=Lato:wght@400;700;900&family=Raleway:wght@400;500&display=swap" rel="stylesheet">
<style>
:root{
  --red:#f04a50;
  --red-soft:#f6a3a6;
  --dark:#2b2b2b;
  --darker:#232323;
  --nav:#3a3a3a;
  --ink:#333;
  --muted:#777;
  --line:#d7d7d7;
  --white:#fff;
}
*{box-sizing:border-box;margin:0;padding:0}
html,body{width:1200px;height:3103px;overflow:hidden}
body{font-family:"Lato",Arial,sans-serif;color:var(--ink);background:var(--white);position:relative}
.heading{font-family:"Raleway",Arial,sans-serif;font-variant:small-caps;letter-spacing:2px;font-weight:500}
section,header,footer{position:relative;width:1200px}

/* header */
.site-header{height:168px;background:var(--red)}
.brand{position:absolute;left:86px;top:44px;color:var(--white);font-family:"Raleway",sans-serif;font-size:24px;line-height:30px;letter-spacing:3px;font-weight:400}
.brand-mark{display:inline-block;width:14px;height:14px;border:2px solid var(--white);margin-right:10px;vertical-align:2px}
.contact-bar{position:absolute;right:86px;top:46px;display:flex;gap:28px;color:var(--white);font-size:16px;align-items:center}
.contact-bar span{display:flex;align-items:center;gap:12px}
.contact-bar svg{width:36px;height:36px}
.main-nav{position:absolute;left:87px;top:132px;width:1023px;height:68px;background:var(--nav);display:flex;justify-content:space-around;align-items:center;padding:0 20px;z-index:2}
.main-nav a{color:#ddd;text-decoration:none;font-size:15px;letter-spacing:1px}
.main-nav a.active{color:var(--red)}

/* hero */
.hero{height:392px;background:linear-gradient(120deg,#8c6a48 0%,#b38d63 35%,#d4c3a9 60%,#6c7a88 100%)}
.hero-shade{position:absolute;inset:0;background:rgba(30,30,30,.35)}
.hero-content{position:absolute;left:0;right:0;top:120px;text-align:center;color:var(--white)}
.hero-title{font-size:50px;font-weight:900;letter-spacing:.5px}
.hero-sub{font-size:21px;margin-top:10px}
.btn-red{display:inline-block;background:var(--red);color:var(--white);font-size:16px;font-weight:700;padding:14px 30px;margin-top:24px}
.slide-arrow{position:absolute;top:178px;width:34px;height:34px;border-radius:50%;background:var(--white)}
.slide-arrow svg{width:34px;height:34px}
.slide-arrow.prev{left:20px}.slide-arrow.next{right:20px}

/* what we do */
.services{height:477px}
.section-title{text-align:center;font-size:32px;color:#222;padding-top:62px}
.title-rule{width:160px;height:3px;background:var(--red);margin:14px auto 0}
.service-list{position:absolute;top:172px;left:0;right:0;height:280px}
.service{position:absolute;width:270px;text-align:center;top:0}
.service-icon{width:146px;height:146px;margin:0 auto;border-radius:50%;border:6px solid #d9d9d9;background:#bdbdbd;display:flex;align-items:center;justify-content:center;box-shadow:inset 0 0 0 8px #fff}
.service.highlight .service-icon{border-color:var(--red);background:var(--red)}
.service-icon svg{width:70px;height:70px}
.service-name{font-size:17px;margin-top:24px;color:#222;font-family:"Raleway",sans-serif;font-variant:small-caps;letter-spacing:1.5px}
.service-desc{font-size:13px;color:var(--muted);line-height:20px;margin-top:8px}

/* who */
.who{height:523px;display:flex}
.who-photo{width:600px;height:523px;background:linear-gradient(135deg,#e8eef0 0%,#d6dde0 40%,#c8b8ae 70%,#9aa3a8 100%)}
.who-panel{width:600px;background:var(--red);color:var(--white);padding:60px 60px 0 48px;position:relative}
.who-panel::before{content:"";position:absolute;left:-22px;top:242px;border-right:22px solid var(--red);border-top:22px solid transparent;border-bottom:22px solid transparent}
.who-title{font-size:32px}
.who-text{font-size:13px;line-height:31px;font-weight:700;margin-top:34px}
.btn-white{display:inline-block;background:var(--white);color:#333;font-size:15px;font-weight:700;padding:16px 42px;margin-top:36px}

/* logos */
.clients{height:670px}
.section-sub{text-align:center;font-size:13px;margin-top:52px}
.logo-grid{position:absolute;left:87px;width:1024px;display:grid;grid-template-columns:repeat(4,240px);column-gap:21px;row-gap:23px}
.clients .logo-grid{top:240px}
.logo-card{height:120px;background:var(--white);border:1px solid var(--line);display:flex;align-items:center;justify-content:center;gap:10px;font-size:24px;font-weight:700;color:#444}
.logo-card i{width:16px;height:16px;background:var(--red);display:inline-block}
.pager{position:absolute;left:0;right:0;display:flex;justify-content:center;gap:28px}
.pager span{width:44px;height:44px;border-radius:50%;display:flex;align-items:center;justify-content:center}
.pager svg{width:18px;height:18px}
.clients .pager{top:543px}
.pager .on{background:var(--red)}
.pager .off{background:var(--red-soft)}

.partners{height:525px;background:var(--red);color:var(--white)}
.partners .section-title{color:var(--white);padding-top:66px}
.partners .section-sub{margin-top:38px}
.partners .logo-grid{top:233px}
.partners .logo-card{border:none}
.partners .pager{top:405px}
.partners .pager .on{background:var(--white)}
.partners .pager .off{background:#f7b6b8}

/* footer */
.site-footer{height:265px;background:var(--dark);color:#ccc}
.footer-brand{position:absolute;left:86px;top:118px;color:var(--white);font-family:"Raleway",sans-serif;font-size:22px;letter-spacing:3px}
.footer-col{position:absolute;top:38px}
.footer-col h3{font-size:16px;color:#eee;font-weight:400;margin-bottom:18px}
.col-news{left:423px;width:210px}
.email-field{height:44px;background:#3d4148;border:1px solid #4a4f57;color:#888;font-size:12px;padding:14px 18px}
.subscribe{margin-top:14px;height:44px;background:var(--red);color:var(--white);text-align:center;line-height:44px;font-size:17px;font-family:"Raleway",sans-serif;font-variant:small-caps;letter-spacing:1px}
.col-contact{left:715px;width:260px}
.col-contact li{list-style:none;display:flex;gap:18px;font-size:12px;line-height:20px;margin-bottom:14px}
.col-contact svg{width:14px;height:14px;flex:none;margin-top:3px}
.col-map{left:1038px}
.col-map li{list-style:none;font-size:12px;line-height:24px}
.bottom-bar{position:absolute;left:0;top:3020px;width:1200px;height:83px;background:var(--darker);border-top:1px solid #3a3a3a;display:flex;align-items:center;justify-content:center;gap:16px;color:#ccc;font-size:12px}
.social{display:flex;gap:12px}
.social i{width:10px;height:10px;border-radius:50%;background:#ccc;display:block}
</style>
</head>
<body>

<header class="site-header">
  <div class="brand"><span class="brand-mark"></span>Brightmoor Counsel</div>
  <div class="contact-bar">
    <span><svg viewBox="0 0 36 36"><circle cx="18" cy="18" r="16" fill="none" stroke="#fff" stroke-width="2"/><path d="M13 11l3 0 1.5 4-2 1.5a9 9 0 0 0 4 4l1.5-2 4 1.5 0 3a2 2 0 0 1-2 2A13 13 0 0 1 11 13a2 2 0 0 1 2-2z" fill="#fff"/></svg>+44(0)20 7946 0321</span>
    <span><svg viewBox="0 0 36 36"><circle cx="18" cy="18" r="16" fill="none" stroke="#fff" stroke-width="2"/><rect x="10" y="12" width="16" height="12" fill="#fff"/><path d="M10 12l8 7 8-7" fill="none" stroke="#f04a50" stroke-width="1.5"/></svg>sales@brightmoor-counsel.com</span>
  </div>
  <nav class="main-nav heading">
    <a class="active" href="#">Home</a><a href="#">What we do</a><a href="#">How we do it</a><a href="#">Who are we</a><a href="#">Why use us</a><a href="#">Clients</a><a href="#">Partners</a><a href="#">Contact</a>
  </nav>
</header>

<section class="hero" role="img" aria-label="Team working together around a wooden office desk with laptops">
  <div class="hero-shade"></div>
  <div class="hero-content">
    <h1 class="hero-title">Interim Management</h1>
    <p class="hero-sub">For Funds, Brokers, Vendors and IT Services Providers</p>
    <span class="btn-red">Read More</span>
  </div>
  <span class="slide-arrow prev"><svg viewBox="0 0 34 34"><path d="M19 11l-6 6 6 6" fill="none" stroke="#333" stroke-width="2.5"/></svg></span>
  <span class="slide-arrow next"><svg viewBox="0 0 34 34"><path d="M15 11l6 6-6 6" fill="none" stroke="#333" stroke-width="2.5"/></svg></span>
</section>

<section class="services">
  <h2 class="section-title heading">What we do</h2>
  <div class="title-rule"></div>
  <div class="service-list">
    <div class="service" style="left:58px">
      <div class="service-icon"><svg viewBox="0 0 70 70"><circle cx="35" cy="30" r="17" fill="none" stroke="#fff" stroke-width="4"/><rect x="28" y="50" width="14" height="8" fill="#fff"/><text x="35" y="38" text-anchor="middle" font-size="22" font-weight="700" fill="#fff" font-family="Lato,sans-serif">$</text></svg></div>
      <div class="service-name">Advice</div>
      <div class="service-desc">Board Level Advisory<br>&amp; Programme Management</div>
    </div>
    <div class="service" style="left:327px">
      <div class="service-icon"><svg viewBox="0 0 70 70"><circle cx="22" cy="22" r="7" fill="#fff"/><circle cx="48" cy="22" r="7" fill="#fff"/><circle cx="35" cy="18" r="8" fill="#fff"/><rect x="12" y="32" width="46" height="14" rx="6" fill="#fff"/><circle cx="22" cy="55" r="7" fill="none" stroke="#fff" stroke-width="4"/><circle cx="48" cy="55" r="7" fill="none" stroke="#fff" stroke-width="4"/></svg></div>
      <div class="service-name">Product Development</div>
      <div class="service-desc">Front-office Trading Platforms &amp;<br>Market Data Pre | At | Post Trade Risk</div>
    </div>
    <div class="service highlight" style="left:594px">
      <div class="service-icon"><svg viewBox="0 0 70 70"><circle cx="35" cy="14" r="7" fill="#fff"/><path d="M35 22v12M15 34h40M15 34v8M35 34v8M55 34v8" stroke="#fff" stroke-width="3" fill="none"/><circle cx="15" cy="50" r="6" fill="#fff"/><circle cx="35" cy="50" r="6" fill="#fff"/><circle cx="55" cy="50" r="6" fill="#fff"/></svg></div>
      <div class="service-name">Interim Management</div>
      <div class="service-desc">For Funds, Brokers, Vendors<br>and IT Services providers</div>
    </div>
    <div class="service" style="left:862px">
      <div class="service-icon"><svg viewBox="0 0 70 70"><path d="M15 35a20 20 0 0 1 34-14" fill="none" stroke="#fff" stroke-width="4"/><path d="M52 14v10h-10" fill="none" stroke="#fff" stroke-width="4"/><path d="M55 35a20 20 0 0 1-34 14" fill="none" stroke="#fff" stroke-width="4"/><path d="M18 56V46h10" fill="none" stroke="#fff" stroke-width="4"/><circle cx="35" cy="35" r="7" fill="#fff"/></svg></div>
      <div class="service-name">Process Outsourcing</div>
      <div class="service-desc">RFI, RFP &amp; Independent tender<br>evaluations (assess before you invest)</div>
    </div>
  </div>
</section>

<section class="who">
  <div class="who-photo" role="img" aria-label="Smiling consultant seated at a laptop in a bright office"></div>
  <div class="who-panel">
    <h2 class="who-title heading">Who are we</h2>
    <p class="who-text">Since founding Brightmoor Counsel in 2014 we have dedicated ourselves to the provision of services. What differentiates us from other advisers or consultancies is a genuine motivation to see our clients succeed. Today's technology allows our clients to take their knowledge to the market in ways that previous generations could only dream of. That's why Brightmoor is dedicated to seeing you choose the right technology strategy, ensuring you maintain a competitive edge over your peers.</p>
    <span class="btn-white">Read More</span>
  </div>
</section>

<section class="clients">
  <h2 class="section-title heading">Clients</h2>
  <p class="section-sub">You will find an impressive list of clients that Brightmoor have worked with.</p>
  <div class="logo-grid">
    <div class="logo-card">Northvale</div>
    <div class="logo-card">Keystone Reach</div>
    <div class="logo-card">Portlane Labs</div>
    <div class="logo-card">Cellar Memory</div>
    <div class="logo-card">Tradewind Hub</div>
    <div class="logo-card"><i></i>Harbor Capital</div>
    <div class="logo-card">Marrow Systems</div>
    <div class="logo-card"><i></i>Quillon Tech</div>
  </div>
  <div class="pager">
    <span class="on"><svg viewBox="0 0 18 18"><path d="M11 3l-6 6 6 6" fill="none" stroke="#fff" stroke-width="3"/></svg></span>
    <span class="off"><svg viewBox="0 0 18 18"><path d="M7 3l6 6-6 6" fill="none" stroke="#fff" stroke-width="3"/></svg></span>
  </div>
</section>

<section class="partners">
  <h2 class="section-title heading">Our Partners</h2>
  <p class="section-sub">Impressive list of partners, working together, building solutions to drive business</p>
  <div class="logo-grid">
    <div class="logo-card">Tradewind Hub</div>
    <div class="logo-card">Keystone Reach</div>
    <div class="logo-card"><i></i>Fennick Link</div>
    <div class="logo-card">Tempometrics</div>
  </div>
  <div class="pager">
    <span class="on"><svg viewBox="0 0 18 18"><path d="M11 3l-6 6 6 6" fill="none" stroke="#f04a50" stroke-width="3"/></svg></span>
    <span class="off"><svg viewBox="0 0 18 18"><path d="M7 3l6 6-6 6" fill="none" stroke="#f04a50" stroke-width="3"/></svg></span>
  </div>
</section>

<footer class="site-footer">
  <div class="footer-brand">Brightmoor Counsel</div>
  <div class="footer-col col-news">
    <h3 class="heading">Newsletter</h3>
    <div class="email-field">Your Email</div>
    <div class="subscribe">Subscribe</div>
  </div>
  <div class="footer-col col-contact">
    <h3 class="heading">Contact Us</h3>
    <ul>
      <li><svg viewBox="0 0 14 14"><path d="M7 1a4 4 0 0 1 4 4c0 3-4 8-4 8S3 8 3 5a4 4 0 0 1 4-4z" fill="#fff"/></svg>Suite 4 Alder Court, Fenwick Park,<br>Bucks, MK19 2QT</li>
      <li><svg viewBox="0 0 14 14"><path d="M3 1h2.5l1 3-1.5 1a7 7 0 0 0 4 4l1-1.5 3 1V11a1.5 1.5 0 0 1-1.5 1.5A10 10 0 0 1 1.5 2.5 1.5 1.5 0 0 1 3 1z" fill="#fff"/></svg>+44(0)20 7946 0321</li>
      <li><svg viewBox="0 0 14 14"><rect x="1" y="3" width="12" height="9" fill="#fff"/><path d="M1 3l6 5 6-5" fill="none" stroke="#2b2b2b" stroke-width="1.2"/></svg>sales@brightmoor-counsel.com</li>
    </ul>
  </div>
  <div class="footer-col col-map">
    <h3 class="heading">Sitemap</h3>
    <ul>
      <li>What we do</li><li>How we do it</li><li>Who are we</li><li>Why use us</li><li>Clients</li><li>Partners</li>
    </ul>
  </div>
</footer>
<div class="bottom-bar">
  <span>Brightmoor Counsel Copyright © 2017. All Rights Reserved.</span>
  <span>|</span>
  <span class="social"><i></i><i></i><i></i><i></i><i></i></span>
</div>

</body>
</html>
```